Letter head for peronal trainer

Letter head top and bottom. Elite looking design that looks modern and prestigious for high end clients. Black, silver, reds etc. Attached are my business cards (2 x pdfs) and my website is: www.doriankemble.net for style/ideas

Needs to look good when printing and be locked onto the page when people use my word docs on the computer, I don't want it to be 'clickable' if you know what I mean. Needs to work in A4 in portrait (and in landscape, for programme cards). I need it to be editable for when I adjust the text myself. Needs my contact details and social media details and title personal trainer (Central Halden/Marrowick/Fenbury) and Online Distance Coaching. . A little picture at the bottom too if it works (Like the vest one)

```html
<!DOCTYPE html>
<html lang="en">
<head>
<meta charset="utf-8">
<title>Dorian Kemble – Letterhead</title>
<link href="https://fonts.googleapis.com/css2?family=Oswald:wght@600;700&family=Arimo:wght@400;700&display=swap" rel="stylesheet">
<style>
  :root {
    --ink: #000000;
    --paper: #ffffff;
    --silver: #c9c9c9;
    --silver-light: #ededed;
    --grey-text: #6a6a6a;
    --rule: #333333;
  }
  html, body { margin: 0; padding: 0; overflow: hidden; background: var(--paper); }
  .sheet {
    position: relative;
    width: 927px; height: 1200px;
    overflow: hidden;
    background: var(--paper);
    font-family: "Arimo", Arial, sans-serif;
    color: var(--ink);
  }
  .header-wave { position: absolute; left: 0; top: 0; width: 927px; height: 290px; }
  .header-photo {
    position: absolute; left: 0; top: 0; width: 182px; height: 222px;
    background: radial-gradient(ellipse at 45% 45%, #8a8a8a 0%, #444 45%, #111 80%);
    clip-path: path("M0 0 H182 V200 C140 214 110 222 70 212 C40 204 18 192 0 180 Z");
  }
  .header-text {
    position: absolute; right: 48px; top: 34px;
    text-align: right; color: var(--paper);
  }
  .header-name {
    font-family: "Oswald", "Arial Narrow", sans-serif;
    font-weight: 700; font-size: 33px; line-height: 38px;
    letter-spacing: 0.5px; margin: 0;
    background: linear-gradient(#ffffff 45%, #bdbdbd);
    -webkit-background-clip: text; background-clip: text; color: transparent;
  }
  .header-title { font-weight: 700; font-size: 14px; letter-spacing: 2.6px; line-height: 17px; margin: 0; }
  .header-service { font-weight: 700; font-size: 13.5px; line-height: 16px; letter-spacing: 0.3px; margin: 0; }
  .header-area { font-size: 14px; line-height: 17px; margin: 0; }

  .footer-photo {
    position: absolute; left: 0; top: 738px; width: 280px; height: 437px;
    background: linear-gradient(180deg, #ffffff 0%, #e6e6e6 20%, #cfcfcf 55%, #d9d9d9 85%, #f4f4f4 100%);
    -webkit-mask-image: linear-gradient(90deg, #000 70%, transparent);
    mask-image: linear-gradient(90deg, #000 70%, transparent);
  }
  .footer-brand {
    position: absolute; left: 498px; top: 1062px;
    font-family: "Oswald", "Arial Narrow", sans-serif; font-weight: 700;
    font-size: 38px; line-height: 31px; letter-spacing: -0.5px;
  }
  .footer-brand .first { color: var(--ink); display: block; }
  .footer-brand .last { color: var(--grey-text); display: block; }
  .footer-credentials {
    position: absolute; left: 638px; top: 1074px;
    font-size: 8px; line-height: 12px; color: #222;
  }
  .footer-frame {
    position: absolute; left: 285px; top: 1101px; width: 601px; height: 67px;
    border-right: 1px solid var(--rule); border-bottom: 1px solid var(--rule);
  }
  .footer-frame::before {
    content: ""; position: absolute; left: 336px; right: 0; top: 0;
    border-top: 1px solid var(--rule);
  }
  .contact-row {
    position: absolute; top: 1151px; left: 0; width: 927px; height: 16px;
    font-size: 11px; color: #222;
  }
  .contact-item { position: absolute; display: flex; align-items: center; gap: 5px; white-space: nowrap; }
  .contact-item svg { flex: none; }
  .contact-phone { left: 292px; font-size: 12px; }
  .contact-email { left: 418px; }
  .contact-web { left: 597px; }
  .contact-social { left: 763px; }
  .footer-band { position: absolute; left: 0; top: 1175px; width: 927px; height: 25px; background: var(--ink); }
</style>
</head>
<body>
<div class="sheet">
  <svg class="header-wave" viewBox="0 0 927 290" aria-hidden="true">
    <defs>
      <linearGradient id="swoosh" x1="0" y1="0" x2="0" y2="1">
        <stop offset="0" stop-color="#9a9a9a"/>
        <stop offset="1" stop-color="#ffffff"/>
      </linearGradient>
      <linearGradient id="swoosh-right" x1="0" y1="0" x2="0" y2="1">
        <stop offset="0" stop-color="#d0d0d0"/>
        <stop offset="1" stop-color="#ffffff"/>
      </linearGradient>
    </defs>
    <path d="M0 182 C20 230 60 270 115 277 C170 282 230 250 300 215 C250 232 180 240 120 236 C70 230 30 210 0 182 Z" fill="url(#swoosh)"/>
    <path d="M380 160 C500 130 640 125 760 160 C820 178 870 195 927 210 C860 180 780 150 700 142 C600 134 480 142 380 160 Z" fill="url(#swoosh-right)"/>
    <path d="M0 0 H927 V210 C860 180 790 150 700 135 C610 122 520 127 430 150 C330 175 250 205 170 216 C100 224 40 205 0 180 Z" fill="var(--ink)"/>
  </svg>
  <div class="header-photo" role="img" aria-label="Black and white portrait photo of the trainer, shirtless, looking aside"></div>
  <div class="header-text">
    <h1 class="header-name">DORIAN KEMBLE</h1>
    <p class="header-title">PERSONAL TRAINER</p>
    <p class="header-service">ONLINE DISTANCE COACHING</p>
    <p class="header-area">Central Halden/Marrowick/Fenbury</p>
  </div>

  <div class="footer-photo" role="img" aria-label="Faded black and white photo of the trainer standing shirtless"></div>

  <div class="footer-brand"><span class="first">DORIAN</span><span class="last">KEMBLE</span></div>
  <div class="footer-credentials">Ex National Athlete &amp; Air Officer<br>Fitness Model &amp; Physique Competitor</div>
  <div class="footer-frame"></div>

  <div class="contact-row">
    <span class="contact-item contact-phone">
      <svg width="8" height="11" viewBox="0 0 8 11"><path d="M2 0 L4 2.5 L3 4 C3.5 6 4.5 7.5 6 8.5 L7 7.5 L8 9.5 L6.5 11 C3 10 0.5 6 0.5 2 Z" fill="#222"/></svg>
      07700900418
    </span>
    <span class="contact-item contact-email">
      <svg width="11" height="11" viewBox="0 0 11 11"><circle cx="5.5" cy="5.5" r="4.8" fill="none" stroke="#222" stroke-width="1"/><path d="M0.7 5.5 H10.3 M5.5 0.7 V10.3 M2 2.8 C4 4 7 4 9 2.8 M2 8.2 C4 7 7 7 9 8.2" stroke="#222" stroke-width="0.8" fill="none"/></svg>
      kemble.dkPT@postmail.net
    </span>
    <span class="contact-item contact-web">
      <svg width="12" height="8" viewBox="0 0 12 8"><rect width="12" height="8" fill="#222"/><path d="M0 0 L6 4.5 L12 0" stroke="#fff" stroke-width="0.9" fill="none"/></svg>
      www.doriankemble.net
    </span>
    <span class="contact-item contact-social">
      <svg width="10" height="10" viewBox="0 0 10 10"><circle cx="5" cy="5" r="5" fill="#222"/></svg>
      @kembly_17
    </span>
  </div>

  <div class="footer-band"></div>
</div>
</body>
</html>
```